Now Hiring Drivers or Help Wanted Ad

I am looking for an ad to be used for digital marketing for employment. Below is some or all of the information to work into the ad.

KORVAN Holdings, LLC is a stable and premier hauler operating in the Northeast Wisconsin region since 1994. We have a variety of equipment from Dump Trucks, Roll Off Trucks to Semis with Belt Trailers, Walking Floors, Gondolas, Tankers, Vans and Compacting Trailers offering a variety of positions with different routes to mix up your day or settle into something you enjoy. We also offer low boy services and some flat bed work. We haul various materials from general aggregate freight to various types of non-hazardous wastes such as garbage, recyclables, paper mill sludge, metal, shredder fluff to various landfills or recycling centers.

Rate of pay is based on experience and the variety of equipment you are able to operate or your willingness to learn.

All work is local and you are home every night.

Great Pay
Sign on Bonus
Holiday & Vacation Pay
Health Insurance, Vision & Dental Offered
Employer Paid Life Insurance
Uniforms
Phone Reimbursement
MERIDO

Industry/Entity Type

Trucking and Excavation

Colors
EB3D1F
EC4F4E
F09395
F8D3D4
FCEDEE

Requirements
Must have
• Should have some of the same look/feel of the ad attached.

```html
<!DOCTYPE html>
<html lang="en">
<head>
<meta charset="utf-8">
<title>KORVAN Holdings – Hiring Drivers</title>
<link href="https://fonts.googleapis.com/css2?family=Poppins:wght@300;400;600;700;800;900&display=swap" rel="stylesheet">
<style>
  :root {
    --green: #52b45f;
    --yellow: #f2c31c;
    --ink: #2f2f2f;
    --black: #0d0d0d;
    --white: #ffffff;
    --text: #3a3a3a;
  }
  * { margin: 0; padding: 0; box-sizing: border-box; }
  html, body { width: 848px; height: 1200px; overflow: hidden; background: var(--white); }
  body { font-family: "Poppins", sans-serif; }
  .poster { position: relative; width: 848px; height: 1200px; overflow: hidden; background: var(--white); }
  .backdrop { position: absolute; inset: 0; }

  .headline { position: absolute; left: 236px; top: 120px; line-height: 0.86; font-weight: 900; letter-spacing: -4px; }
  .headline span { display: block; font-size: 150px; }
  .headline .hiring { color: var(--white); }
  .headline .drivers { color: var(--green); margin-left: -4px; }

  .why-title { position: absolute; left: 434px; top: 496px; font-size: 36px; font-weight: 300; color: var(--green); letter-spacing: -0.5px; }
  .why-title strong { color: var(--black); font-weight: 800; }

  .list { list-style: none; position: absolute; }
  .list li { position: relative; font-weight: 700; color: var(--ink); }
  .list li::before { content: ""; position: absolute; border-radius: 50%; background: var(--green); }

  .benefits { left: 478px; top: 552px; width: 340px; }
  .benefits li { font-size: 21px; line-height: 28px; margin-bottom: 4.5px; }
  .benefits li::before { width: 16px; height: 16px; left: -35px; top: 6px; }

  .equipment-title { position: absolute; left: 39px; top: 582px; font-size: 34px; font-weight: 700; color: var(--green); line-height: 36px; letter-spacing: -0.5px; }
  .equipment { left: 78px; top: 668px; width: 300px; }
  .equipment li { font-size: 17px; line-height: 23px; margin-bottom: 4px; }
  .equipment li::before { width: 13px; height: 13px; left: -28px; top: 5px; }

  .body-copy { position: absolute; font-size: 15px; line-height: 20px; color: var(--text); font-weight: 400; }
  .haul { left: 43px; top: 864px; width: 303px; text-align: justify; }
  .pay { left: 434px; top: 890px; width: 340px; }
  .local { left: 503px; top: 966px; width: 240px; }

  .brand { position: absolute; left: 300px; top: 977px; width: 206px; height: 206px; display: flex; align-items: center; justify-content: center; }
  .brand-name { font-size: 30px; font-weight: 800; color: var(--green); letter-spacing: -0.5px; }

  .call { position: absolute; left: 43px; top: 1078px; color: var(--white); font-weight: 700; line-height: 1.25; }
  .call .label { font-size: 31px; letter-spacing: -0.5px; }
  .call .number { font-size: 32px; letter-spacing: -0.5px; }

  .social { position: absolute; left: 571px; top: 1122px; width: 220px; text-align: center; color: var(--white); font-size: 12px; font-weight: 600; letter-spacing: 0.6px; }
</style>
</head>
<body>
<main class="poster">
  <svg class="backdrop" width="848" height="1200" viewBox="0 0 848 1200" xmlns="http://www.w3.org/2000/svg">
    <defs>
      <linearGradient id="photoTone" x1="0" y1="0" x2="1" y2="1">
        <stop offset="0" stop-color="#8c8f92"/>
        <stop offset="0.45" stop-color="#a3242a"/>
        <stop offset="0.8" stop-color="#5a4c4a"/>
        <stop offset="1" stop-color="#9aa0a4"/>
      </linearGradient>
    </defs>
    <rect class="photo" role="img" aria-label="Photo of a driver in a hi-vis shirt standing beside a red dump truck" x="0" y="0" width="848" height="560" fill="url(#photoTone)"/>
    <path class="wave-green" d="M0 440 C120 530 260 520 380 450 C520 380 680 370 848 400 L848 1200 L0 1200 Z" fill="var(--green)"/>
    <path class="wave-yellow" d="M400 468 C540 390 720 375 848 440 L848 560 C760 470 600 440 400 468 Z" fill="var(--yellow)"/>
    <path class="field-white" d="M0 528 C130 545 250 510 370 470 C520 420 680 410 848 470 L848 1200 L0 1200 Z" fill="var(--white)"/>
    <path class="wedge-green" d="M848 890 C800 1000 700 1060 540 1072 L848 1090 Z" fill="var(--green)"/>
    <path class="footer" d="M0 1048 C120 1026 240 1020 330 1035 L470 1035 C600 1070 740 1075 848 1040 L848 1200 L0 1200 Z" fill="var(--black)"/>
    <circle cx="403" cy="1080" r="115" fill="var(--black)"/>
    <circle cx="403" cy="1080" r="103" fill="var(--white)"/>
    <g class="social-icons">
      <circle cx="675" cy="1100" r="18" fill="var(--green)"/>
      <circle cx="720" cy="1100" r="18" fill="var(--green)"/>
      <circle cx="764" cy="1100" r="18" fill="var(--green)"/>
      <path d="M757 1092 c2-2 4-2 5 0 l2 3 c1 1 0 3-1 4 c1 3 3 5 6 6 c1-1 3-2 4-1 l3 2 c2 1 2 3 0 5 c-3 3-9 1-14-4 c-5-5-7-11-5-15 z" fill="var(--black)"/>
    </g>
  </svg>

  <h1 class="headline"><span class="hiring">HIRING</span><span class="drivers">DRIVERS</span></h1>

  <h2 class="why-title">WHY CHOOSE <strong>US!</strong></h2>
  <ul class="list benefits">
    <li>Great Pay</li>
    <li>Sign on Bonus</li>
    <li>Holiday &amp; Vacation Pay</li>
    <li>Health Insurance, Vision &amp; Dental Offered</li>
    <li>Tankers</li>
    <li>Employer Paid Life Insurance</li>
    <li>Uniforms</li>
    <li>Phone Reimbursement</li>
    <li>MERIDO</li>
  </ul>

  <h2 class="equipment-title">We have a variety<br>of equipment from</h2>
  <ul class="list equipment">
    <li>Dump Trucks</li>
    <li>Roll Off Trucks to Semis with Belt Trailers</li>
    <li>Walking Floors</li>
    <li>Gondolas</li>
    <li>Tankers</li>
    <li>Vans and Compacting Trailers</li>
  </ul>

  <p class="body-copy haul">We haul various materials from general aggregate freight to various types of non-hazardous wastes such as garbage, recyclables, paper mill sludge, metal, shredder fluff to various landfills or recycling centers.</p>
  <p class="body-copy pay">Rate of pay is based on experience and the variety of equipment you are able to operate or your willingness to learn.</p>
  <p class="body-copy local">All work is local and you are home every night.</p>

  <div class="brand"><span class="brand-name">KORVAN</span></div>

  <div class="call">
    <div class="label">CALL US</div>
    <div class="number">+00 123 456 789</div>
  </div>
  <div class="social">@Socialmedia / 0123 456 789</div>
</main>
</body>
</html>
```